Redesign current business card for food company

i would like to redesign my business card. our company is food company, our product range from chips, juices, milk and etc (mostly dried food stuff).
I want o keep same logo but , the rest is open to new design.
you can check at our website about our company www.orvelpantry.com

Target Market(s)

most of food company

Industry/Entity Type

Business

Contact Information for Business Card

I want to keep more to blue color...

Colors
3176b5
abd036

Requirements
Must have
• our old logo
Nice to have
• we do not mind to have nice material on bus card in order to accomplish nice design. for example: using spot uv, embossed and etc.

```html
<!DOCTYPE html>
<html lang="en">
<head>
<meta charset="utf-8">
<title>Orvel business card</title>
<link href="https://fonts.googleapis.com/css2?family=Open+Sans:wght@400;600;700&display=swap" rel="stylesheet">
<style>
  :root {
    --backdrop: #ece9e4;
    --card-black: #0e0e0f;
    --card-black-soft: #1b1b1d;
    --brand-blue: #2a8fd6;
    --accent-yellow: #f8c91c;
    --text-white: #ffffff;
    --text-soft: #e6e6e6;
  }
  * { margin: 0; padding: 0; box-sizing: border-box; }
  html, body { width: 1200px; height: 900px; overflow: hidden; }
  body {
    background: var(--backdrop);
    font-family: "Open Sans", Arial, sans-serif;
    position: relative;
  }
  .card {
    position: absolute;
    width: 665px;
    height: 380px;
    left: 267px;
    border-radius: 4px;
    overflow: hidden;
    background: radial-gradient(ellipse at 40% 30%, var(--card-black-soft), var(--card-black) 70%);
    box-shadow: 0 6px 18px rgba(0,0,0,0.18);
  }
  .card--front { top: 45px; }
  .card--back { top: 475px; }

  .wordmark {
    color: var(--text-white);
    font-weight: 600;
    line-height: 1;
    white-space: nowrap;
  }
  .card--front .wordmark {
    position: absolute;
    left: 50%; top: 50%;
    transform: translate(-50%, -55%);
    font-size: 96px;
  }
  .card--back .wordmark {
    position: absolute;
    right: 42px; top: 46px;
    font-size: 52px;
  }

  .card__wave { position: absolute; inset: 0; width: 100%; height: 100%; }

  .contact {
    position: absolute;
    left: 40px; top: 38px;
    color: var(--text-white);
  }
  .contact__name {
    color: var(--brand-blue);
    font-weight: 700;
    font-size: 19px;
  }
  .contact__role { font-size: 14px; margin: 2px 0 0 4px; }
  .contact__lines { list-style: none; margin: 20px 0 0 20px; }
  .contact__lines li {
    display: flex; align-items: center; gap: 8px;
    font-size: 15px; line-height: 21px; color: var(--text-soft);
  }
  .contact__lines svg { width: 12px; height: 12px; fill: var(--brand-blue); flex: none; }
  .contact__company {
    margin: 18px 0 0 20px;
    color: var(--brand-blue);
    font-weight: 600;
    font-size: 15px;
  }
  .contact__address { margin-left: 20px; font-size: 15px; color: var(--text-soft); }

  .card__url {
    position: absolute;
    right: 36px; top: 222px;
    color: var(--text-white);
    font-size: 12px;
  }
</style>
</head>
<body>

  <section class="card card--front" aria-label="Card front">
    <p class="wordmark">Orvel</p>
  </section>

  <section class="card card--back" aria-label="Card back">
    <svg class="card__wave" viewBox="0 0 665 380" preserveAspectRatio="none" aria-hidden="true">
      <path d="M0,318 C210,352 390,300 490,225 C560,172 620,150 665,146 L665,380 L0,380 Z" fill="var(--brand-blue)"/>
      <path d="M0,292 C220,328 390,280 480,200 C410,285 230,330 0,314 Z" fill="var(--accent-yellow)"/>
    </svg>

    <p class="wordmark">Orvel</p>

    <div class="contact">
      <p class="contact__name">Daniel Surawijaya</p>
      <p class="contact__role">President</p>
      <ul class="contact__lines">
        <li><svg viewBox="0 0 12 12"><path d="M1 4c0-2 2-3 5-3s5 1 5 3l-2 1-1-2H4L3 5zM2 6h8v5H2z"/></svg>909 555 0142</li>
        <li><svg viewBox="0 0 12 12"><path d="M3 1h6v3H3zM1 5h10v6H1zM3 8h6v1H3z"/></svg>909 555 0187</li>
        <li><svg viewBox="0 0 12 12"><path d="M3 0h6v12H3zM4 1v8h4V1z"/></svg>626 555 0139</li>
        <li><svg viewBox="0 0 12 12"><path d="M0 2h12v8H0zM1 3l5 4 5-4z"/></svg>Daniel@orvelpantry.com</li>
      </ul>
      <p class="contact__company">Orvel Enterprises Corp.</p>
      <p class="contact__address">1480 W Cedar Ave.Fairview CA 91700</p>
    </div>

    <p class="card__url">www.orvelpantry.com</p>
  </section>

</body>
</html>
```